Maple Grove Schools | brand new stationery!

We need stationery design with our new logo! Our company updated it's name and image and we like to incorporate the new one on our stationery, business cards and email signature. We are looking for fresh, new ideas!
Industry: Childcare, Elementary and Middle School
Company Name: Maple Grove Schools
Tagline: Bright Futures Start Here
Main colors: Blue, white and a little yellow
Star shape is something new for us! Do you see a way to incorporate it as a design element?

```html
<!DOCTYPE html>
<html lang="en">
<head>
<meta charset="utf-8">
<title>Maple Grove Schools – Business Card</title>
<link rel="stylesheet" href="https://fonts.googleapis.com/css2?family=Poppins:wght@400;500;600&display=swap">
<style>
  :root {
    --navy: #0b1a75;
    --yellow: #f7b611;
    --ink: #1a1a1a;
    --paper: #ffffff;
    --stage: #2a2b2e;
    --muted: #3a3a44;
  }
  * { margin: 0; padding: 0; box-sizing: border-box; }
  html, body { width: 1200px; height: 874px; overflow: hidden; }
  body {
    background: var(--stage);
    font-family: "Poppins", sans-serif;
    position: relative;
  }
  .card {
    position: absolute;
    left: 270px;
    width: 660px;
    height: 378px;
    border-radius: 22px;
    overflow: hidden;
  }
  .card-back { top: 39px; background: var(--navy); color: var(--paper); }
  .card-front { top: 457px; background: var(--paper); color: var(--ink); }

  /* back */
  .back-brand {
    position: absolute;
    left: 0; right: 0; top: 118px;
    display: flex; flex-direction: column; align-items: center; gap: 14px;
  }
  .back-brand .brand-dot { width: 34px; height: 34px; border-radius: 50%; background: var(--paper); }
  .back-brand .brand-name { font-size: 30px; font-weight: 600; color: var(--paper); line-height: 1.1; }
  .back-url {
    position: absolute; left: 0; right: 0; bottom: 46px;
    text-align: center; font-size: 15px; letter-spacing: 4px; font-weight: 500;
  }

  /* front */
  .front-brand {
    position: absolute; left: 58px; top: 96px;
    display: flex; flex-direction: column; align-items: flex-start; gap: 12px;
  }
  .front-brand .brand-dot { width: 30px; height: 30px; border-radius: 50%; background: var(--navy); margin-left: 70px; }
  .front-brand .brand-name { font-size: 34px; font-weight: 600; color: var(--ink); line-height: 1.05; }

  .contact { position: absolute; left: 392px; top: 48px; width: 250px; }
  .person-name { font-size: 22px; font-weight: 500; color: var(--navy); letter-spacing: 1px; line-height: 1; }
  .person-role { font-size: 14px; color: var(--yellow); margin-top: 2px; }
  .contact-list { list-style: none; margin-top: 14px; }
  .contact-list li {
    display: flex; align-items: flex-start; gap: 8px;
    font-size: 14px; line-height: 19px; color: var(--muted);
  }
  .contact-list li.address { margin-bottom: 6px; }
  .contact-list svg { width: 12px; height: 12px; flex: none; margin-top: 4px; fill: var(--navy); }

  .wave { position: absolute; left: 0; top: 0; width: 660px; height: 378px; }
</style>
</head>
<body>

<section class="card card-back">
  <div class="back-brand">
    <span class="brand-dot"></span>
    <span class="brand-name">Maple Grove Schools</span>
  </div>
  <p class="back-url">WWW.MAPLEGROVESCHOOLS.COM</p>
</section>

<section class="card card-front">
  <svg class="wave" viewBox="0 0 660 378" aria-hidden="true">
    <path d="M0,262 C140,330 330,350 660,352 L660,378 L0,378 Z" fill="var(--navy)"/>
    <path d="M0,248 C150,322 330,338 660,344" fill="none" stroke="var(--yellow)" stroke-width="7"/>
    <path d="M250,318 C420,332 560,330 660,318 L660,342 C560,340 420,338 250,318 Z" fill="var(--ink)"/>
  </svg>

  <div class="front-brand">
    <span class="brand-dot"></span>
    <span class="brand-name">Maple Grove<br>Schools</span>
  </div>

  <div class="contact">
    <p class="person-name">DANIEL HART</p>
    <p class="person-role">President</p>
    <ul class="contact-list">
      <li class="address">
        <svg viewBox="0 0 12 12"><path d="M6 0a4 4 0 0 0-4 4c0 3 4 8 4 8s4-5 4-8a4 4 0 0 0-4-4zm0 5.5A1.5 1.5 0 1 1 6 2.5a1.5 1.5 0 0 1 0 3z"/></svg>
        <span>4210 Willow Bend Road<br>Fairbanks, Alaska 99701</span>
      </li>
      <li>
        <svg viewBox="0 0 12 12"><path d="M2.5 0.5l2 0 1 3-1.5 1a7 7 0 0 0 3.5 3.5l1-1.5 3 1 0 2a1.5 1.5 0 0 1-1.5 1.5A10 10 0 0 1 1 2a1.5 1.5 0 0 1 1.5-1.5z"/></svg>
        <span>555-218-4071</span>
      </li>
      <li>
        <svg viewBox="0 0 12 12"><path d="M3 0h6a1 1 0 0 1 1 1v10a1 1 0 0 1-1 1H3a1 1 0 0 1-1-1V1a1 1 0 0 1 1-1zm0.5 1.5v8h5v-8z"/></svg>
        <span>555-630-2194</span>
      </li>
      <li>
        <svg viewBox="0 0 12 12"><path d="M3 0h6v3H3zM1 4h10v6H9V8H3v2H1zM3 9h6v3H3z"/></svg>
        <span>555-472-8816</span>
      </li>
      <li>
        <svg viewBox="0 0 12 12"><path d="M0 2h12v8H0zM1 3l5 3.5L11 3v-0.2H1z"/></svg>
        <span>info@maplegroveschools.com</span>
      </li>
      <li>
        <svg viewBox="0 0 12 12"><circle cx="6" cy="6" r="6"/></svg>
        <span>maplegroveschools.com</span>
      </li>
    </ul>
  </div>
</section>

</body>
</html>
```